Construction business card

I need a new business card, they can connect with my logo, brand.
What we do is residential house , design and build
I like: Navy blue / black
I attached our logo, brand,
and, some idea for business card.

```html
<!DOCTYPE html>
<html lang="en">
<head>
<meta charset="utf-8">
<title>Norvale Building Group – Business Card</title>
<link rel="stylesheet" href="https://fonts.googleapis.com/css2?family=Arimo:wght@400;700&family=Varela+Round&display=swap">
<style>
  :root {
    --page-bg: #cfe7e8;
    --card-white: #ffffff;
    --navy: #020a26;
    --line-navy: #141a3c;
    --accent-blue: #3d86c9;
    --text-dark: #1d1d1f;
    --logo-grey: #a9adb8;
    --logo-white: #ffffff;
  }
  * { box-sizing: border-box; margin: 0; padding: 0; }
  html, body { width: 1200px; height: 1200px; overflow: hidden; }
  body {
    background: var(--page-bg);
    font-family: "Arimo", Arial, sans-serif;
    display: flex;
    flex-direction: column;
    align-items: center;
    justify-content: center;
    gap: 48px;
  }
  .card {
    position: relative;
    width: 880px;
    height: 503px;
    overflow: hidden;
    box-shadow: 0 12px 30px rgba(20, 40, 60, 0.18);
  }
  .card--front { background: var(--card-white); }
  .card--back { background: var(--navy); }

  .rule { position: absolute; }
  .card--front .rule--v1 { left: 72px; top: 0; bottom: 0; width: 4px; background: var(--line-navy); }
  .card--front .rule--v2 { left: 46px; top: 168px; bottom: 0; width: 4px; background: var(--line-navy); }
  .card--front .rule--h { left: 0; right: 0; bottom: 60px; height: 3px; background: var(--accent-blue); }

  .card--back .rule--v1 { left: 54px; top: 0; bottom: 0; width: 3px; background: var(--accent-blue); }
  .card--back .rule--v2 { left: 84px; top: 200px; bottom: 0; width: 3px; background: var(--accent-blue); }
  .card--back .rule--h { left: 0; right: 0; bottom: 44px; height: 3px; background: var(--accent-blue); }

  .person { position: absolute; left: 122px; top: 150px; }
  .person__name {
    font-family: "Varela Round", Arial, sans-serif;
    font-size: 46px;
    color: var(--accent-blue);
    letter-spacing: 1px;
    line-height: 1;
  }
  .person__role { font-size: 16px; color: var(--text-dark); margin-top: 2px; }

  .contact { position: absolute; left: 116px; top: 272px; list-style: none; }
  .contact__item {
    display: flex;
    align-items: flex-start;
    gap: 18px;
    font-size: 19px;
    color: var(--text-dark);
    line-height: 1.3;
    margin-bottom: 4px;
  }
  .contact__item--address { margin-bottom: 22px; }
  .contact__icon { width: 22px; height: 22px; flex: none; margin-top: 1px; }

  .brand {
    position: absolute;
    display: flex;
    flex-direction: column;
    align-items: center;
    font-family: "Arimo", Arial, sans-serif;
    font-weight: 700;
    text-transform: uppercase;
    line-height: 1;
  }
  .brand__name { font-size: 78px; letter-spacing: 3px; }
  .brand__tag { font-size: 30px; letter-spacing: 4px; margin-top: 10px; }
  .card--front .brand { right: 60px; top: 170px; color: var(--logo-grey); }
  .card--back .brand { left: 0; right: 0; top: 180px; color: var(--logo-white); }
</style>
</head>
<body>

<section class="card card--front" aria-label="Business card front">
  <span class="rule rule--v1"></span>
  <span class="rule rule--v2"></span>
  <span class="rule rule--h"></span>

  <div class="person">
    <h1 class="person__name">Sam Carter</h1>
    <p class="person__role">Manager</p>
  </div>

  <ul class="contact">
    <li class="contact__item contact__item--address">
      <svg class="contact__icon" viewBox="0 0 24 24" aria-hidden="true"><path fill="#3d86c9" d="M12 2a7 7 0 0 0-7 7c0 5 7 13 7 13s7-8 7-13a7 7 0 0 0-7-7zm0 9.5A2.5 2.5 0 1 1 12 6.5a2.5 2.5 0 0 1 0 5z"/></svg>
      <span>48 Harrow Street,<br>Eastmoor, Vic 3190</span>
    </li>
    <li class="contact__item">
      <svg class="contact__icon" viewBox="0 0 24 24" aria-hidden="true"><path fill="#3d86c9" d="M6.6 10.8a15 15 0 0 0 6.6 6.6l2.2-2.2a1 1 0 0 1 1-.25 11.4 11.4 0 0 0 3.6.57 1 1 0 0 1 1 1V20a1 1 0 0 1-1 1A17 17 0 0 1 3 4a1 1 0 0 1 1-1h3.5a1 1 0 0 1 1 1c0 1.25.2 2.45.57 3.6a1 1 0 0 1-.25 1z"/></svg>
      <span>0400 555 218</span>
    </li>
    <li class="contact__item">
      <svg class="contact__icon" viewBox="0 0 24 24" aria-hidden="true"><path fill="#3d86c9" d="M3 5h18v14H3zm2 2v.5l7 4.5 7-4.5V7l-7 4.5z"/></svg>
      <span>info@norvalebuilding.com.au</span>
    </li>
    <li class="contact__item">
      <svg class="contact__icon" viewBox="0 0 24 24" aria-hidden="true"><g fill="none" stroke="#3d86c9" stroke-width="1.8"><circle cx="12" cy="12" r="9"/><ellipse cx="12" cy="12" rx="4" ry="9"/><path d="M3 12h18M5 7h14M5 17h14"/></g></svg>
      <span>www.norvalebuilding.com.au</span>
    </li>
  </ul>

  <div class="brand">
    <span class="brand__name">Norvale</span>
    <span class="brand__tag">Building Group</span>
  </div>
</section>

<section class="card card--back" aria-label="Business card back">
  <span class="rule rule--v1"></span>
  <span class="rule rule--v2"></span>
  <span class="rule rule--h"></span>

  <div class="brand">
    <span class="brand__name">Norvale</span>
    <span class="brand__tag">Building Group</span>
  </div>
</section>

</body>
</html>
```